Stationery Design Project for Marketing Consultancy

I have started a new consultancy business and require the following elements to be designed using existing logo:
• Business card
• Letterhead
• Envelope (DL, C4, C5)
• Microsoft word template for report writing
• A4 Presentation Folder
• Powerpoint template
COPY FOR FRONT AND BACK OF BUSINESS CARD
logo
'Measurable Marketing. Epic Results' slogan (but no need to use existing lockup with logo)
name, B Bus. Mktg, Grad Dip Digital Mktg, CPM (post nominal abbreviations in smaller font)
mobile: 04XX-XXX-XXX (I will give details to the winner to add)
website: www.tolvarin.com.au
email: info@tolvarin.com.au
COPY FOR LETTERHEAD
Logo
Company Name
Please, submit your designs that include business card, letterhead and envelope. Once selected the winner will be asked to complete the project by creating the rest of the artwork.
FINAL FILES
Print ready files to be supplied as well as Indesign files so that minor amends can be made if necessary in future.
• Layered vectors in EPS & PDF
• Screen quality JPEG & PNGs
ABOUT THE BUSINESS: TOLVARIN
I work with clients to understand their business challenges, developing and executing measurable marketing strategies tied to key business metrics. Services include:
Services include:
• Business planning and business development
• Marketing and brand strategy
• Insight-driven integrated campaigns
• Loyalty programs and retention marketing
• Marketing automation
• Direct marketing (traditional and digital)
• Content strategy and development
Hi everyone,
Target Market(s)
Corporate decision makers (heads of marketing, general managers etc) and small to medium sized business owners. Predominately male aged 35+
Industry/Entity Type
Marketing
Requirements
Must have
- BRAND PERSONALITY
The successful design will communicate brand personality. I am a professional, results-driven entrepreneur, but want to show off my creative flair.
MEMORABILITY
Looking for a unique and eye-catching design. Am considering special printing effects (die cuts, letterpress, interactive elements, embossing, foiling etc) or a striking minimalist approach.
Nice to have
- I have a mission that could be incorporated on reverse if room -
Turning insights into actions & passion into profit.
Should not have
- Use of pink or green.

```html
<!DOCTYPE html>
<html lang="en">
<head>
<meta charset="utf-8">
<title>Tolvarin Business Card</title>
<link href="https://fonts.googleapis.com/css2?family=Source+Sans+3:wght@400;600;700&display=swap" rel="stylesheet">
<style>
  :root {
    --page: #ffffff;
    --card-light: #f1f1f1;
    --card-dark-top: #2b2b2b;
    --card-dark-bottom: #1b1b1b;
    --ink: #1e1e1e;
    --ink-soft: #3a3a3a;
    --accent: #f04e1a;
    --white: #ffffff;
  }
  * { box-sizing: border-box; margin: 0; padding: 0; }
  html, body {
    width: 1200px;
    height: 907px;
    overflow: hidden;
    background: var(--page);
    font-family: "Source Sans 3", "Myriad Pro", Arial, sans-serif;
    color: var(--ink);
  }
  .canvas { position: relative; width: 1200px; height: 907px; }

  .card { position: absolute; left: 300px; width: 600px; height: 352px; background: var(--card-light); }
  .card--front { top: 78px; }
  .card--back { top: 476px; }

  .front__brand-panel {
    position: absolute; left: 0; top: 0; width: 352px; height: 352px;
    background: linear-gradient(135deg, var(--card-dark-top), var(--card-dark-bottom));
  }
  .brand-mark {
    position: absolute; left: 126px; top: 92px; width: 100px; height: 100px;
    border-radius: 50%; background: var(--white);
  }
  .brand-name {
    position: absolute; left: 0; width: 352px; top: 222px;
    text-align: center; color: var(--white);
    font-weight: 700; font-size: 44px; letter-spacing: 1px; line-height: 1;
  }

  .slogan { position: absolute; left: 384px; top: 214px; color: var(--ink); }
  .slogan__lead { font-size: 17px; line-height: 22px; }
  .slogan__main { font-size: 28px; line-height: 34px; letter-spacing: 1.2px; }

  .contact { position: absolute; left: 50px; top: 140px; }
  .contact__name { font-size: 17px; color: var(--accent); line-height: 22px; }
  .contact__name strong { font-weight: 600; }
  .contact__credentials { font-size: 10.5px; color: var(--ink-soft); margin-top: 3px; }
  .contact__list { list-style: none; margin-top: 22px; font-size: 16.5px; line-height: 22px; }
  .contact__label { display: inline-block; width: 24px; color: var(--accent); font-weight: 700; }

  .back-mark {
    position: absolute; left: 379px; top: 98px; width: 82px; height: 82px;
    border-radius: 50%; background: var(--ink);
  }
  .back-name {
    position: absolute; left: 330px; width: 180px; top: 190px; text-align: center;
    font-size: 18px; font-weight: 600; letter-spacing: 1px; color: var(--ink);
  }
  .mission {
    position: absolute; left: 320px; width: 200px; top: 227px;
    text-align: center; color: var(--ink);
  }
  .mission__line1 { font-size: 16px; line-height: 22px; }
  .mission__line2 { font-size: 17.5px; line-height: 24px; }
</style>
</head>
<body>
<main class="canvas">
  <section class="card card--front" aria-label="Business card front">
    <div class="front__brand-panel">
      <div class="brand-mark" aria-hidden="true"></div>
      <div class="brand-name">TOLVARIN</div>
    </div>
    <div class="slogan">
      <p class="slogan__lead">Measurable Marketing.</p>
      <p class="slogan__main">Epic Results.</p>
    </div>
  </section>

  <section class="card card--back" aria-label="Business card back">
    <div class="contact">
      <p class="contact__name"><strong>Liam</strong> Hartley</p>
      <p class="contact__credentials">B Bus. Mktg, Grad Dip Digital Mktg, CPM</p>
      <ul class="contact__list">
        <li><span class="contact__label">M</span>0400 555 018</li>
        <li><span class="contact__label">W</span>www.tolvarin.com.au</li>
        <li><span class="contact__label">E</span>info@tolvarin.com.au</li>
      </ul>
    </div>
    <div class="back-mark" aria-hidden="true"></div>
    <div class="back-name">TOLVARIN</div>
    <div class="mission">
      <p class="mission__line1">Turning insights into action</p>
      <p class="mission__line2">and passion into profit.</p>
    </div>
  </section>
</main>
</body>
</html>
```